Brand Identity Stationary Package

Hello I'm looking for a full branding package for my Property Management Company. I have a logo but looking to have the following
Business Card
Email signature
Facebook cover photo
Letterhead (word.doc)
#10 Envelope
Pocket Folder - link to 9x12 pocket folder design specs https://www.printorbit-example.ca/marketing-materials/presentation-folders
would like everything to match and be brand identifiable. The company looks after residential properties/apartments and some commercial properties. Attached is a zip of the files.
For Business Card
Name: Gareth Lindqvist
Position: Operations Manager
Number: 1 (555) 384-2917
Email: Gareth@harborkey-example.ca
Website: Harborkey-example.ca
Property Management

```html
<!DOCTYPE html>
<html lang="en">
<head>
<meta charset="utf-8">
<title>Harborkey Property Management — #10 Envelope</title>
<link rel="stylesheet" href="https://fonts.googleapis.com/css2?family=Montserrat:wght@500;600&family=Open+Sans:wght@400&display=swap">
<style>
  :root {
    --brand-green: #80a641;
    --ink: #161616;
    --paper: #f3f2f2;
    --paper-light: #ffffff;
    --backdrop: #d0cfcf;
    --on-green: #f4f4f2;
  }
  * { margin: 0; padding: 0; box-sizing: border-box; }
  html, body { width: 1200px; height: 1050px; overflow: hidden; }
  body { background: var(--backdrop); position: relative; font-family: "Open Sans", sans-serif; }

  .envelope {
    position: absolute;
    left: 145px;
    width: 910px;
    height: 390px;
    background: radial-gradient(ellipse at 50% 85%, var(--paper-light) 0%, var(--paper-light) 20%, var(--paper) 65%);
    box-shadow: 0 14px 22px rgba(0,0,0,0.22);
    overflow: hidden;
  }
  .envelope--back { top: 105px; }
  .envelope--front { top: 556px; background: radial-gradient(ellipse at 50% 0%, var(--paper-light) 0%, var(--paper) 55%); }

  .envelope__art { position: absolute; inset: 0; width: 100%; height: 100%; }

  .wordmark {
    position: absolute;
    font-family: "Montserrat", sans-serif;
    font-weight: 600;
    line-height: 1;
  }
  .wordmark__name { display: block; }
  .wordmark__tagline {
    display: block;
    font-weight: 500;
  }

  .envelope--back .wordmark {
    left: 0; right: 0; top: 32px;
    text-align: center;
    color: var(--on-green);
  }
  .envelope--back .wordmark__name { font-size: 46px; letter-spacing: 5px; }
  .envelope--back .wordmark__tagline { font-size: 10.5px; letter-spacing: 8.6px; margin-top: 10px; padding-left: 8px; }

  .envelope--front .wordmark {
    left: 52px; top: 62px;
    color: var(--ink);
  }
  .envelope--front .wordmark__name { font-size: 38px; letter-spacing: 4px; }
  .envelope--front .wordmark__tagline { font-size: 9.5px; letter-spacing: 7.6px; margin-top: 8px; }

  .contact-list {
    position: absolute;
    left: 52px; top: 145px;
    list-style: none;
    color: var(--ink);
    font-size: 19px;
  }
  .contact-list__item {
    display: flex;
    align-items: center;
    height: 26px;
  }
  .contact-list__icon {
    width: 16px; height: 16px;
    margin-right: 13px;
    fill: var(--brand-green);
  }
</style>
</head>
<body>

  <section class="envelope envelope--back">
    <svg class="envelope__art" viewBox="0 0 910 390" aria-hidden="true">
      <path d="M0 0 H910 L888 90 Q876 131 830 131 H80 Q34 131 24 90 Z" fill="var(--brand-green)"/>
    </svg>
    <div class="wordmark">
      <span class="wordmark__name">HARBORKEY</span>
      <span class="wordmark__tagline">PROPERTY MANAGEMENT</span>
    </div>
  </section>

  <section class="envelope envelope--front">
    <svg class="envelope__art" viewBox="0 0 910 390" aria-hidden="true">
      <path d="M0 303 C150 325 350 312 520 262 C690 212 800 170 910 212 V228 C800 192 690 230 520 278 C350 328 150 336 0 315 Z" fill="var(--ink)"/>
      <path d="M0 320 C150 345 350 326 520 282 C690 238 800 210 910 240 V390 H0 Z" fill="var(--brand-green)"/>
    </svg>

    <div class="wordmark">
      <span class="wordmark__name">HARBORKEY</span>
      <span class="wordmark__tagline">PROPERTY MANAGEMENT</span>
    </div>

    <ul class="contact-list">
      <li class="contact-list__item">
        <svg class="contact-list__icon" viewBox="0 0 16 16" aria-hidden="true">
          <path d="M1 6 Q8 1 15 6 L13 8 L11 6.5 V5 Q8 4 5 5 V6.5 L3 8 Z"/>
          <rect x="3" y="8" width="10" height="7" rx="1"/>
        </svg>
        1 (555) 384-2917
      </li>
      <li class="contact-list__item">
        <svg class="contact-list__icon" viewBox="0 0 16 16" aria-hidden="true">
          <path d="M0 3 H16 V13 H0 Z M1.5 4.5 L8 9 L14.5 4.5 Z" fill-rule="evenodd"/>
        </svg>
        Gareth@harborkey-example.ca
      </li>
      <li class="contact-list__item">
        <svg class="contact-list__icon" viewBox="0 0 16 16" aria-hidden="true">
          <circle cx="8" cy="8" r="7.5"/>
          <path d="M4 4 Q6 3 7 5 Q5 7 6 9 Q4 9 3 7 Z M10 9 Q12 8 13 10 Q12 13 10 13 Q9 11 10 9 Z" fill="var(--paper-light)"/>
        </svg>
        www.Harborkey-example.ca
      </li>
    </ul>
  </section>

</body>
</html>
```